Income Tax Business Cards - Updates

Need to update these business cards while keeping all the same wording but just update them and make them look nicer and more modern/ on brand with our brand.

Industry/Entity Type

finance

Contact Information for Business Card

we have multiple locations so will just need to easily be able to change the address and phone numbers

Colors

Designer to choose colors to be used in the design.

```html
<!DOCTYPE html>
<html lang="en">
<head>
<meta charset="UTF-8">
<title>Ledgerline Financial Group – Tax Advance Business Cards</title>
<link rel="stylesheet" href="https://fonts.googleapis.com/css2?family=Arimo:wght@400;700&family=Tinos:wght@400;700&display=swap">
<style>
  :root {
    --brand-green: #1b5631;
    --brand-green-deep: #144527;
    --brand-red: #b81e25;
    --paper: #f4f4f2;
    --ink-white: #ffffff;
    --backdrop: #e6e4e0;
    --serif: "Tinos", "Times New Roman", serif;
    --sans: "Arimo", Arial, sans-serif;
  }
  * { box-sizing: border-box; margin: 0; padding: 0; }
  html, body { width: 1200px; height: 912px; overflow: hidden; }
  body {
    background: var(--backdrop);
    position: relative;
    font-family: var(--sans);
  }
  .card {
    position: absolute;
    width: 640px;
    height: 366px;
    border-radius: 22px;
    overflow: hidden;
    box-shadow: 0 10px 28px rgba(0,0,0,.18);
  }
  .card--front { left: 80px; top: 48px; background: var(--brand-green); }
  .card--back  { left: 480px; top: 498px; background: var(--brand-green); }

  /* Front */
  .brand-name {
    position: absolute;
    font-family: var(--serif);
    font-weight: 400;
    color: var(--ink-white);
    white-space: nowrap;
  }
  .card--front .brand-name {
    left: 0; right: 0; top: 40px;
    text-align: center;
    font-size: 30px;
  }
  .front-band {
    position: absolute;
    left: 0; right: 0; top: 112px;
    height: 64px;
    background: var(--brand-red);
    display: flex; align-items: center; justify-content: center;
  }
  .front-band__text {
    font-family: var(--serif);
    font-weight: 700;
    font-size: 44px;
    color: var(--ink-white);
  }
  .front-offer {
    position: absolute;
    left: 0; right: 0; top: 196px;
    text-align: center;
    color: var(--ink-white);
  }
  .offer-amount {
    font-family: var(--sans);
    font-weight: 700;
    font-size: 66px;
    line-height: 1;
  }
  .offer-speed {
    font-family: var(--serif);
    font-weight: 700;
    font-size: 42px;
    line-height: 1.15;
  }

  /* Back */
  .back-shape { position: absolute; inset: 0; }
  .back-offer {
    position: absolute;
    left: 38px; top: 40px;
  }
  .back-offer__headline {
    font-family: var(--serif);
    font-weight: 700;
    font-size: 40px;
    color: var(--brand-red);
    line-height: 1.1;
  }
  .card--back .offer-amount { color: var(--brand-green); font-size: 62px; margin-top: 10px; }
  .card--back .offer-speed { color: var(--brand-red); font-size: 38px; }
  .back-offer__note {
    font-family: var(--sans);
    font-size: 17px;
    color: var(--brand-green-deep);
    margin-top: 2px;
  }
  .card--back .brand-name {
    right: 24px; top: 158px;
    font-size: 21px;
    line-height: 28px;
    text-align: right;
  }
  .contact-phone {
    position: absolute;
    right: 24px; top: 224px;
    display: flex; align-items: center; gap: 8px;
    font-family: var(--sans);
    font-weight: 700;
    font-size: 22px;
    color: var(--ink-white);
  }
  .contact-phone svg { width: 18px; height: 18px; }
  .contact-address {
    position: absolute;
    left: 38px; bottom: 22px;
    font-family: var(--sans);
    font-size: 17px;
    color: var(--ink-white);
  }
</style>
</head>
<body>

  <section class="card card--front" aria-label="Business card front">
    <div class="brand-name">Ledgerline Financial Group</div>
    <div class="front-band"><span class="front-band__text">File your Taxes here</span></div>
    <div class="front-offer">
      <div class="offer-amount">UP to $6000</div>
      <div class="offer-speed">Same day advance</div>
    </div>
  </section>

  <section class="card card--back" aria-label="Business card back">
    <svg class="back-shape" viewBox="0 0 640 366" width="640" height="366" aria-hidden="true">
      <path d="M0 0 H568 C558 204 330 296 0 302 Z" fill="#b81e25"/>
      <path d="M0 0 H560 C550 196 322 288 0 294 Z" fill="#f4f4f2"/>
    </svg>
    <div class="back-offer">
      <div class="back-offer__headline">Free Estimates!</div>
      <div class="offer-amount">UP to $6000</div>
      <div class="offer-speed">Same day advance</div>
      <div class="back-offer__note">on approved tax returns!</div>
    </div>
    <div class="brand-name">Ledgerline<br>Financial Group</div>
    <div class="contact-phone">
      <svg viewBox="0 0 24 24" aria-hidden="true"><path fill="#ffffff" d="M6.6 10.8a15.1 15.1 0 0 0 6.6 6.6l2.2-2.2a1 1 0 0 1 1-.25 11.4 11.4 0 0 0 3.6.57 1 1 0 0 1 1 1V20a1 1 0 0 1-1 1A17 17 0 0 1 3 4a1 1 0 0 1 1-1h3.5a1 1 0 0 1 1 1c0 1.25.2 2.45.57 3.57a1 1 0 0 1-.25 1z"/></svg>
      <span>(555) 010-4821</span>
    </div>
    <div class="contact-address">2170 Harbor View Lane, Millbrook, NY 12545</div>
  </section>

</body>
</html>
```